Visit card

Industry/Entity Type

Health Care

Contact Information for Business Card

O VITALIS SYSTEMS
Odile Brevard - chef de Projet

Requirements
Must have
• 318 Gaston Lemaire Street 59710 SAULNERAY Tel: 33 (0) 327 481 605 Mobile: 06 42 19 37 64 Web: www.quorvexsystems.example Contact: o.brevard@o-vitalissystems.example
Should not have
• Respect for color

```html
<!DOCTYPE html>
<html lang="fr">
<head>
<meta charset="utf-8">
<title>O Vitalis Systems – Carte de visite</title>
<link rel="stylesheet" href="https://fonts.googleapis.com/css2?family=Lato:wght@400;700;900&display=swap">
<style>
  :root {
    --backdrop: #1c1c1c;
    --card: #232323;
    --card-front: #262626;
    --red: #e3212d;
    --white: #f4f4f4;
    --grey: #9a9a9a;
    --emboss: #1a1a1a;
  }
  html, body {
    margin: 0;
    width: 1200px;
    height: 900px;
    overflow: hidden;
    background: var(--backdrop);
    font-family: "Lato", sans-serif;
  }
  .canvas {
    position: relative;
    width: 1200px;
    height: 900px;
  }
  .card {
    position: absolute;
    left: 250px;
    width: 700px;
    height: 400px;
    box-shadow: 0 18px 40px rgba(0,0,0,.55);
  }
  .card--front {
    top: 40px;
    background: linear-gradient(160deg, #2b2b2b, var(--card-front) 60%, #202020);
    display: flex;
    align-items: center;
    justify-content: center;
    gap: 26px;
  }
  .card--back {
    top: 460px;
    background: var(--card);
  }
  .mark {
    border-radius: 50%;
    flex: none;
  }
  .card--front .mark {
    width: 110px;
    height: 110px;
    background: var(--emboss);
    box-shadow: inset 2px 2px 4px rgba(0,0,0,.6), 1px 1px 0 rgba(255,255,255,.06);
  }
  .brand-name {
    font-weight: 900;
    letter-spacing: 1px;
    line-height: 1.05;
    text-transform: uppercase;
  }
  .card--front .brand-name {
    font-size: 40px;
    color: var(--grey);
  }
  .back-brand {
    position: absolute;
    left: 52px;
    top: 152px;
    display: flex;
    align-items: center;
    gap: 20px;
  }
  .card--back .mark {
    width: 92px;
    height: 92px;
    background: var(--white);
  }
  .card--back .brand-name {
    font-size: 30px;
    color: var(--red);
  }
  .divider {
    position: absolute;
    left: 396px;
    top: 110px;
    width: 2px;
    height: 180px;
    background: var(--white);
  }
  .contact {
    position: absolute;
    left: 422px;
    top: 100px;
    color: var(--white);
    font-size: 15px;
    line-height: 1.35;
  }
  .contact__name {
    margin: 0;
    font-size: 23px;
    font-weight: 700;
    color: var(--red);
    text-transform: uppercase;
    letter-spacing: .5px;
  }
  .contact__role { margin: 0 0 10px; font-size: 15px; }
  .contact__address { margin: 0 0 10px; font-style: normal; }
  .contact__list { list-style: none; margin: 0; padding: 0; }
  .contact__list li { display: flex; align-items: center; gap: 8px; }
  .contact__list svg { width: 11px; height: 11px; flex: none; }
</style>
</head>
<body>
<main class="canvas">
  <section class="card card--front">
    <span class="mark"></span>
    <span class="brand-name">O Vitalis<br>Systems</span>
  </section>

  <section class="card card--back">
    <div class="back-brand">
      <span class="mark"></span>
      <span class="brand-name">O Vitalis<br>Systems</span>
    </div>
    <span class="divider"></span>
    <div class="contact">
      <p class="contact__name">Odile Brevard</p>
      <p class="contact__role">Chef de Projet</p>
      <address class="contact__address">318 Rue Gaston Lemaire<br>59710 SAULNERAY</address>
      <ul class="contact__list">
        <li><svg viewBox="0 0 12 12" fill="none" stroke="#e3212d" stroke-width="1.6"><path d="M3 1 L5 3 L4 5 Q5 7 7 8 L9 7 L11 9 L9 11 Q3 10 1 3 Z"/></svg>+33 (0) 327 481 605</li>
        <li><svg viewBox="0 0 12 12" fill="none" stroke="#e3212d" stroke-width="1.6"><rect x="3" y="1" width="6" height="10" rx="1"/><line x1="5" y1="9" x2="7" y2="9"/></svg>06 42 19 37 64</li>
        <li><svg viewBox="0 0 12 12" fill="none" stroke="#e3212d" stroke-width="1.2"><circle cx="6" cy="6" r="5"/><ellipse cx="6" cy="6" rx="2" ry="5"/><line x1="1" y1="6" x2="11" y2="6"/></svg>www.quorvexsystems.example</li>
        <li><svg viewBox="0 0 12 12" fill="none" stroke="#e3212d" stroke-width="1.4"><rect x="1" y="2.5" width="10" height="7"/><path d="M1 2.5 L6 7 L11 2.5"/></svg>o.brevard@o-vitalissystems.example</li>
      </ul>
    </div>
  </section>
</main>
</body>
</html>
```